Northfield Builders Guild Business card

We are looking for a new business card design with photo included.
Our business is a nonprofit construction contractor membership organization. We offer business education, assist with business setup and licensing, provide safety training, and provide a member directory.
URL: www.builderslinkguild.org
Color code:
CMYK: 0 cyan, 42 magenta, 100 yellow, 0 black for Print.
Hexidecimal: #FF9900
RGB: R 255; G 153; B 0

```html
<!DOCTYPE html>
<html lang="en">
<head>
<meta charset="utf-8">
<title>Northfield Builders Guild – Business Card</title>
<link rel="stylesheet" href="https://fonts.googleapis.com/css2?family=Montserrat:wght@400;500;800&display=swap">
<style>
  :root {
    --brand-orange: #ff9900;
    --band-orange: #f7941d;
    --ink: #3a3a3a;
    --ink-soft: #555555;
    --card-white: #ffffff;
    --card-dark: #353334;
    --back-text: #b9b9b9;
    --backdrop: #e6e6e6;
    --rule: #9a9a9a;
  }
  * { box-sizing: border-box; margin: 0; padding: 0; }
  html, body {
    width: 1200px; height: 1200px; overflow: hidden;
    background: var(--backdrop);
    font-family: "Montserrat", Arial, sans-serif;
  }
  .canvas { position: relative; width: 1200px; height: 1200px; }

  .card {
    position: absolute; left: 257px; width: 686px; height: 392px;
    border-radius: 22px; overflow: hidden;
  }
  .card--front { top: 165px; background: var(--card-white); }
  .card--back { top: 653px; background: var(--card-dark); }

  .front-band {
    position: absolute; left: 0; right: 0; bottom: 0; height: 14px;
    background: var(--band-orange);
  }

  .wordmark {
    position: absolute; left: 30px; width: 300px; top: 160px;
    text-align: center; color: var(--ink);
    font-weight: 800; letter-spacing: -0.5px; line-height: 1.05;
  }
  .wordmark__line { display: block; font-size: 33px; }
  .wordmark__line--small { font-size: 27px; }

  .divider {
    position: absolute; left: 357px; top: 87px; width: 1px; height: 216px;
    background: var(--rule);
  }

  .contact { position: absolute; left: 384px; top: 88px; color: var(--ink-soft); }
  .contact__name {
    font-size: 23px; font-weight: 500; color: var(--ink); letter-spacing: 0.5px;
    line-height: 1.1;
  }
  .contact__title { font-size: 16px; color: var(--band-orange); margin-top: 2px; }
  .contact__address { font-size: 15.5px; line-height: 19.5px; margin-top: 16px; }
  .contact__list { list-style: none; margin-top: 13px; font-size: 15.5px; line-height: 19.5px; }
  .contact__list li { display: flex; align-items: center; gap: 8px; }
  .contact__icon { width: 13px; height: 13px; flex: none; fill: var(--band-orange); }

  .back-wordmark {
    position: absolute; left: 0; right: 0; top: 142px;
    text-align: center; color: var(--back-text);
    font-weight: 800; letter-spacing: -1px; line-height: 1.02;
  }
  .back-wordmark__line { display: block; font-size: 52px; }
  .back-wordmark__line--small { font-size: 42px; }
</style>
</head>
<body>
<div class="canvas">

  <section class="card card--front" aria-label="Business card front">
    <div class="wordmark">
      <span class="wordmark__line">NORTHFIELD</span>
      <span class="wordmark__line wordmark__line--small">BUILDERS GUILD</span>
    </div>

    <div class="divider"></div>

    <div class="contact">
      <p class="contact__name">DANIEL HAYES</p>
      <p class="contact__title">President</p>
      <p class="contact__address">2400 NW Alder Ave.,<br>Suite #210<br>Salem, OR 97301</p>
      <ul class="contact__list">
        <li>
          <svg class="contact__icon" viewBox="0 0 16 16" aria-hidden="true"><path d="M3.5 1l2.5 3-1.5 2c1 2 3 4 5 5l2-1.5 3 2.5-1.5 2.5C7 15 1 9 1 2.5z"/></svg>
          (555) 214-3080
        </li>
        <li>
          <svg class="contact__icon" viewBox="0 0 16 16" aria-hidden="true"><path d="M4 0h8v16H4zM5.5 2v10h5V2zM7 13.2h2v1.3H7z" fill-rule="evenodd"/></svg>
          555.730.1962
        </li>
        <li>
          <svg class="contact__icon" viewBox="0 0 16 16" aria-hidden="true"><path d="M1 4h14v9H1zM1.5 4.5L8 9l6.5-4.5" /></svg>
          support@nbguild.org
        </li>
        <li>
          <svg class="contact__icon" viewBox="0 0 16 16" aria-hidden="true"><circle cx="8" cy="8" r="7"/><path d="M4 5l3 1 0 3-2 1zM10 9l2 1-1 3-2-1z" fill="#fff"/></svg>
          builderslinkguild.org
        </li>
      </ul>
    </div>

    <div class="front-band"></div>
  </section>

  <section class="card card--back" aria-label="Business card back">
    <div class="back-wordmark">
      <span class="back-wordmark__line">NORTHFIELD</span>
      <span class="back-wordmark__line back-wordmark__line--small">BUILDERS GUILD</span>
    </div>
  </section>

</div>
</body>
</html>
```